CV design and layout with option for text and contact details has be sleek

I have logo just need this to look good on a CV

Target Market(s)

Directors , Production , TV, Film

Industry/Entity Type

tv film cinema advertising

Colors
0054AA
0677BA
7BADD7
CADEEF
E8F1F8

Requirements
Must have
• my logo and contact information
Should not have
• any other images or logos except mine

```html
<!DOCTYPE html>
<html lang="en">
<head>
<meta charset="utf-8">
<title>Rowan Hale ICS – Cinematographer</title>
<link href="https://fonts.googleapis.com/css2?family=Montserrat:wght@400;500;700&display=swap" rel="stylesheet">
<style>
  :root {
    --ink: #000000;
    --label: #333333;
    --accent: #1572e8;
    --paper: #ffffff;
  }
  html, body {
    margin: 0;
    padding: 0;
    overflow: hidden;
    background: var(--paper);
  }
  .canvas {
    position: relative;
    width: 1200px;
    height: 1200px;
    background: var(--paper);
    font-family: "Montserrat", sans-serif;
    overflow: hidden;
  }
  .frame-line {
    position: absolute;
    left: 145px;
    top: 491px;
    width: 913px;
    height: 216px;
    border: 2px solid var(--ink);
    box-sizing: border-box;
  }
  .corner {
    position: absolute;
    background: var(--ink);
  }
  .corner-tl-h { left: 132px; top: 483px; width: 98px; height: 23px; }
  .corner-tl-v { left: 132px; top: 483px; width: 23px; height: 96px; }
  .corner-br-v { left: 1046px; top: 619px; width: 22px; height: 96px; }
  .corner-br-h { left: 971px; top: 694px; width: 97px; height: 21px; }

  .name {
    position: absolute;
    left: 192px;
    top: 580px;
    margin: 0;
    font-size: 30px;
    font-weight: 400;
    color: var(--ink);
    letter-spacing: 0.2px;
    white-space: nowrap;
  }

  .role {
    position: absolute;
    left: 546px;
    top: 506px;
    margin: 0;
    font-size: 17px;
    font-weight: 700;
    letter-spacing: 0.6px;
    color: var(--label);
  }

  .contacts {
    position: absolute;
    left: 546px;
    top: 540px;
    margin: 0;
    padding: 0;
    list-style: none;
  }
  .contact {
    display: flex;
    align-items: center;
    height: 27px;
    margin-bottom: 3.5px;
    font-size: 21px;
    font-weight: 500;
    color: var(--label);
    white-space: nowrap;
  }
  .contact .icon {
    width: 27px;
    height: 27px;
    margin-right: 11px;
    flex: none;
  }
  .contact .value { color: var(--accent); margin-left: 6px; }
  .contact .value.solo { margin-left: 0; }
</style>
</head>
<body>
<main class="canvas">
  <div class="frame-line"></div>
  <div class="corner corner-tl-h"></div>
  <div class="corner corner-tl-v"></div>
  <div class="corner corner-br-v"></div>
  <div class="corner corner-br-h"></div>

  <h1 class="name">ROWAN HALE ICS</h1>

  <p class="role">CINEMATOGRAPHER</p>

  <ul class="contacts">
    <li class="contact">
      <svg class="icon" viewBox="0 0 27 27"><rect x="1" y="1" width="25" height="25" fill="none" stroke="#000" stroke-width="2"/><path d="M9 6 l3 0 l1 4 l-2 1.5 q1.5 4 5 5.5 l1.5 -2 l4 1 l0 3 q-1 1.5 -3 1.5 q-6 -1 -9.5 -8.5 q-0.5 -3 0 -6z" fill="#000"/></svg>
      <span>MOB AUS</span><span class="value">+61 400 555 017</span>
    </li>
    <li class="contact">
      <svg class="icon" viewBox="0 0 27 27"><rect x="1" y="1" width="25" height="25" fill="none" stroke="#000" stroke-width="2"/><path d="M9 6 l3 0 l1 4 l-2 1.5 q1.5 4 5 5.5 l1.5 -2 l4 1 l0 3 q-1 1.5 -3 1.5 q-6 -1 -9.5 -8.5 q-0.5 -3 0 -6z" fill="#000"/></svg>
      <span>MOB US</span><span class="value">+1 555 013 4822</span>
    </li>
    <li class="contact">
      <svg class="icon" viewBox="0 0 27 27"><rect x="1" y="1" width="25" height="25" fill="none" stroke="#000" stroke-width="2"/><path d="M9 6 l3 0 l1 4 l-2 1.5 q1.5 4 5 5.5 l1.5 -2 l4 1 l0 3 q-1 1.5 -3 1.5 q-6 -1 -9.5 -8.5 q-0.5 -3 0 -6z" fill="#000"/></svg>
      <span>AGENT CREWLINE:</span><span class="value">+61 255 501 384</span>
    </li>
    <li class="contact">
      <svg class="icon" viewBox="0 0 27 27"><rect x="1" y="1" width="25" height="25" fill="none" stroke="#000" stroke-width="2"/><rect x="5.5" y="8" width="16" height="11" fill="none" stroke="#000" stroke-width="1.6"/><path d="M5.5 8 l8 6 l8 -6 M5.5 19 l6 -5 M21.5 19 l-6 -5" fill="none" stroke="#000" stroke-width="1.4"/></svg>
      <span class="value solo">rowanhaledop@mailbox.net</span>
    </li>
    <li class="contact">
      <svg class="icon" viewBox="0 0 27 27"><rect x="1" y="1" width="25" height="25" fill="none" stroke="#000" stroke-width="2"/><circle cx="13.5" cy="13.5" r="7.5" fill="none" stroke="#000" stroke-width="1.5"/><ellipse cx="13.5" cy="13.5" rx="3.2" ry="7.5" fill="none" stroke="#000" stroke-width="1.2"/><path d="M6 13.5 h15 M7.2 9.5 h12.6 M7.2 17.5 h12.6" stroke="#000" stroke-width="1.2"/></svg>
      <span class="value solo">www.rowanhale.example</span>
    </li>
  </ul>
</main>
</body>
</html>
```